Business Card Design (NEW FILES)

ATTENTION: New vector files are available. Please update your design to reflect/use the new (better resolution) logo images.

Seeking a unique and professional business card design for a commercial drone photography/videography business. The layout should feature
the logo (attached) and include the following information:
Owen Tarrick
614-502-7738
www.skylarkreelworks.example
NRD Certified Remote Pilot

Owen Tarrick

```html
<!DOCTYPE html>
<html lang="en">
<head>
<meta charset="utf-8">
<title>Skylark Reelworks – Business Card</title>
<link rel="stylesheet" href="https://fonts.googleapis.com/css2?family=Montserrat:wght@500;600&family=Open+Sans:wght@600;700;800&display=swap">
<style>
  :root {
    --backdrop: #232323;
    --orange: #ec8a55;
    --orange-light: #f6a868;
    --orange-deep: #e37840;
    --navy: #1c1f4a;
    --white: #ffffff;
    --grey-shade: #cfd0d4;
  }
  * { margin: 0; padding: 0; box-sizing: border-box; }
  html, body { width: 1200px; height: 780px; overflow: hidden; background: var(--backdrop); }
  .stage {
    position: relative; width: 1200px; height: 780px;
    display: flex; justify-content: center; align-items: center; gap: 70px;
  }
  .card {
    position: relative; width: 320px; height: 560px; border-radius: 22px; overflow: hidden;
    box-shadow: 0 18px 40px rgba(0,0,0,.55);
  }

  /* Front */
  .card-front { background: var(--orange); }
  .front-artwork {
    position: absolute; left: 20px; top: 40px; width: 280px; height: 330px; border-radius: 50%;
    background: radial-gradient(ellipse at 45% 45%, var(--orange-light) 0%, var(--orange) 55%, var(--orange-deep) 100%);
    opacity: .85;
  }
  .front-brand {
    position: absolute; left: 0; right: 0; bottom: 90px;
    display: flex; flex-direction: column; align-items: center; gap: 10px;
  }
  .brand-dot { width: 26px; height: 26px; border-radius: 50%; background: var(--navy); flex: none; }
  .brand-name {
    font-family: "Montserrat", sans-serif; font-weight: 500; color: var(--navy);
    font-size: 24px; letter-spacing: 1px; text-transform: uppercase; text-align: center; line-height: 1.15;
  }

  /* Back */
  .card-back { background: var(--white); }
  .back-brand {
    position: absolute; top: 64px; left: 0; right: 0;
    display: flex; align-items: center; justify-content: center; gap: 12px;
  }
  .back-brand .brand-dot { width: 22px; height: 22px; }
  .back-brand .brand-name { font-size: 21px; text-align: left; }
  .holder { position: absolute; top: 200px; left: 0; right: 0; text-align: center; font-family: "Open Sans", sans-serif; }
  .holder-name { font-weight: 800; font-size: 30px; line-height: 1; }
  .holder-name .first { color: var(--orange); }
  .holder-name .last { color: var(--navy); }
  .holder-role { font-weight: 700; font-size: 14px; color: var(--navy); margin-top: 6px; }
  .contact-icons { display: flex; justify-content: center; gap: 8px; margin-top: 16px; }
  .contact-icons svg { width: 22px; height: 22px; }
  .contact-list { margin-top: 10px; list-style: none; font-weight: 600; font-size: 13px; color: var(--navy); line-height: 1.5; }
  .bottom-bands { position: absolute; left: 0; bottom: 0; width: 320px; height: 200px; }
  .credentials {
    position: absolute; bottom: 46px; left: 0; right: 0; text-align: center;
    font-family: "Open Sans", sans-serif; font-weight: 600; font-size: 14px; color: var(--navy); line-height: 1.45;
  }
</style>
</head>
<body>
<main class="stage">
  <section class="card card-front">
    <div class="front-artwork" role="img" aria-label="Embossed drone illustration with camera aperture"></div>
    <div class="front-brand">
      <span class="brand-dot"></span>
      <span class="brand-name">Skylark<br>Reelworks</span>
    </div>
  </section>

  <section class="card card-back">
    <div class="back-brand">
      <span class="brand-dot"></span>
      <span class="brand-name">Skylark<br>Reelworks</span>
    </div>

    <div class="holder">
      <h1 class="holder-name"><span class="first">Owen</span> <span class="last">Tarrick</span></h1>
      <p class="holder-role">Owner</p>
      <div class="contact-icons">
        <svg viewBox="0 0 22 22" aria-label="Phone"><circle cx="11" cy="11" r="11" fill="var(--orange)"/><path d="M7.5 6.5l2 2-1 1.2c.7 1.4 1.8 2.5 3.2 3.2l1.2-1 2 2-1.2 1.6c-3.6-.4-7-3.8-7.4-7.4z" fill="#fff"/></svg>
        <svg viewBox="0 0 22 22" aria-label="Email"><circle cx="11" cy="11" r="11" fill="var(--orange)"/><rect x="6" y="7.5" width="10" height="7" rx="1" fill="#fff"/><path d="M6.5 8l4.5 3.5L15.5 8" stroke="var(--orange)" fill="none" stroke-width="1"/></svg>
        <svg viewBox="0 0 22 22" aria-label="Website"><circle cx="11" cy="11" r="11" fill="var(--orange)"/><circle cx="11" cy="11" r="5" fill="none" stroke="#fff" stroke-width="1.3"/><path d="M6 11h10M11 6c-2.5 3-2.5 7 0 10M11 6c2.5 3 2.5 7 0 10" stroke="#fff" stroke-width="1" fill="none"/></svg>
      </div>
      <ul class="contact-list">
        <li>614-502-7738</li>
        <li>www.skylarkreelworks.example</li>
        <li>info@skylarkreelworks.example</li>
      </ul>
    </div>

    <svg class="bottom-bands" viewBox="0 0 320 200" preserveAspectRatio="none" aria-hidden="true">
      <defs>
        <linearGradient id="band" x1="0" y1="0" x2="0" y2="1">
          <stop offset="0" stop-color="var(--grey-shade)"/>
          <stop offset="1" stop-color="#fafafa"/>
        </linearGradient>
      </defs>
      <path d="M0 40 Q200 90 320 0 V200 H0 Z" fill="url(#band)"/>
      <path d="M0 70 Q220 120 320 30 V200 H0 Z" fill="#f3f3f4"/>
      <path d="M0 110 Q180 100 320 60 V200 H0 Z" fill="url(#band)" opacity=".6"/>
      <path d="M0 130 Q200 125 320 85 V200 H0 Z" fill="#fbfbfb"/>
    </svg>
    <p class="credentials">NRD Certified Remote Pilot<br>Fully Insured</p>
  </section>
</main>
</body>
</html>
```